Brisk Harbor claims recovery services

Its a new company in Dubai UAE. The company activity is debt management, debt collection, loans settlements and restructuring. The company involved in any business or sector requires debt management including government entities, Medical & Health care sector, Banks & finance companies, SME's and commercial business.

Target Market(s)

government entities, Medical & Health care sector, Banks & finance companies, SME's and commercial business.

Industry/Entity Type

Financial Service

Number of Pages Required

5+ page

Requirements
Must have
• Focus on the services not the team and clients
Should not have
• Colorful . Shouldn't have Client testimonial and our clients

```html
<!DOCTYPE html>
<html lang="en">
<head>
<meta charset="utf-8">
<title>Brisk Harbor – Claims Recovery Services</title>
<link rel="stylesheet" href="https://fonts.googleapis.com/css2?family=Cinzel:wght@400;600;700&family=Lato:wght@700;900&family=Open+Sans:wght@400;600;700&family=Roboto+Condensed:wght@300;400&display=swap">
<style>
:root{
  --navy:#27496d;
  --navy-dark:#234466;
  --grey-bg:#ececec;
  --text:#666666;
  --box-grey:#8e8e8e;
  --white:#ffffff;
  --icon-bg:#e9e9e9;
}
*{margin:0;padding:0;box-sizing:border-box}
html,body{width:1200px;height:3020px;overflow:hidden}
body{position:relative;background:var(--white);font-family:"Open Sans",Arial,sans-serif;color:var(--text)}
.abs{position:absolute}

/* hero */
.hero{left:0;top:0;width:1200px;height:800px}
.hero-photo{position:absolute;inset:0;background:linear-gradient(100deg,#eef1f4 0%,#d9dde2 30%,#9aa3ad 55%,#4e5a68 80%,#2f3947 100%)}
.hero-fade{position:absolute;left:0;top:0;width:1200px;height:120px;background:linear-gradient(#ffffffdd,#ffffff00)}
.brand{left:80px;top:34px;display:flex;align-items:center;gap:16px}
.brand-mark{width:44px;height:44px;background:var(--navy)}
.brand-name{font-family:"Cinzel",serif;font-weight:600;font-size:36px;color:var(--navy);letter-spacing:1px}
.nav{left:467px;top:32px;display:flex;height:53px}
.nav a{font-family:"Cinzel",serif;font-size:19px;color:#1e2a38;text-decoration:none;line-height:53px;padding:0 20px}
.nav a.active{background:var(--navy);color:var(--white)}
.hero-title{left:78px;top:222px;font-family:"Lato",sans-serif;font-weight:900;font-size:41px;line-height:63px;color:var(--navy)}
.btn-outline{left:78px;top:443px;width:196px;height:61px;border:2px solid var(--navy);border-radius:4px;font-family:"Cinzel",serif;font-size:23px;color:var(--navy);display:flex;align-items:center;justify-content:center}

/* welcome */
.welcome-title{left:0;top:908px;width:1200px;text-align:center;font-family:"Cinzel",serif;font-size:47px;color:#8a8a8a}
.welcome-title span{color:var(--navy)}
.welcome-text{left:130px;top:982px;width:940px;text-align:center;font-size:15.5px;line-height:26px}
.sector{top:1093px;width:230px;text-align:center}
.sector-icon{width:114px;height:114px;border-radius:50%;background:var(--icon-bg);margin:0 auto;display:flex;align-items:center;justify-content:center}
.sector-label{margin-top:19px;font-family:"Cinzel",serif;font-size:19px;line-height:32px;color:#222}

/* recovery */
.band-grey{left:0;width:1200px;background:var(--grey-bg)}
.recovery-art{left:100px;top:1378px;width:415px;height:335px;border-radius:20px;background:radial-gradient(ellipse at 50% 60%,#4a7fc2 0%,#8fb0d8 45%,#e4e9ef 75%,#ececec00 100%)}
.section-title{font-family:"Cinzel",serif;font-weight:600;font-size:36px;color:var(--navy);letter-spacing:1px}
.copy{font-size:15.5px;line-height:26px}
.copy p+p{margin-top:26px}
.btn{height:49px;background:var(--navy);color:var(--white);font-family:"Cinzel",serif;font-size:21px;display:flex;align-items:center;justify-content:center;border-radius:2px}

/* diagram */
.node{width:125px;height:83px;background:var(--box-grey);color:var(--white);border-radius:4px;font-size:14.5px;line-height:20px;text-align:center;display:flex;align-items:center;justify-content:center;padding:0 6px}
.node.lead{background:var(--navy);font-weight:700;border-radius:6px}

/* news */
.news-title{left:0;top:2268px;width:1200px;text-align:center;font-family:"Roboto Condensed",sans-serif;font-weight:300;font-size:46px;color:#888}
.news-title span{color:var(--navy);font-weight:400}
.news-card{top:2337px;width:234px}
.news-photo{height:141px}
.news-head{margin-top:10px;font-size:16px;color:#3a6a9a}
.news-date{margin-top:4px;font-size:13.5px;color:#999;display:flex;align-items:center;gap:8px}
.news-text{margin-top:10px;font-size:15.5px;line-height:25px}

/* footer */
.footer{left:0;top:2667px;width:1200px;height:353px;background:var(--navy)}
.footer *{color:var(--white)}
.foot-brand{left:80px;top:2808px;font-family:"Cinzel",serif;font-size:31px;letter-spacing:1px}
.foot-about{left:80px;top:2864px;width:225px;font-size:15px;line-height:26px}
.foot-heading{top:2702px;font-family:"Cinzel",serif;font-size:22px;letter-spacing:1px}
.foot-links{left:350px;top:2745px;list-style:none;font-size:16.5px;line-height:33.4px}
.foot-links li::before{content:"\203A";margin-right:10px;font-size:20px}
.field{left:620px;width:232px;height:35px;background:#3a6690;font-size:14.5px;line-height:35px;padding-left:10px}
.subscribe{left:618px;top:2885px;width:160px;height:47px;background:var(--white);font-family:"Cinzel",serif;font-size:20px;display:flex;align-items:center;justify-content:center;letter-spacing:1px}
.subscribe span{color:var(--navy)}
.contact-row{left:892px;display:flex;gap:14px;font-size:15px;line-height:24px}
.social{top:2886px;width:50px;height:50px;border:2px solid var(--white);border-radius:50%}
.foot-rule{left:80px;top:2966px;width:1040px;height:1px;background:#4a6f95}
.copyright{left:0;top:2983px;width:1200px;text-align:center;font-size:15px}
</style>
</head>
<body>

<header class="abs hero">
  <div class="hero-photo" role="img" aria-label="Photo of two businessmen reviewing documents at a desk with a laptop"></div>
  <div class="hero-fade"></div>
  <div class="abs brand"><div class="brand-mark"></div><div class="brand-name">BRISK HARBOR</div></div>
  <nav class="abs nav">
    <a class="active">HOME</a><a>ABOUT</a><a>SERVICES</a><a>CLIENTS</a><a>BLOG</a><a>CONTACT</a>
  </nav>
  <h1 class="abs hero-title">MANAGING YOUR MONEY,<br>RECOVERING YOUR<br>RELATIONSHIPS</h1>
  <div class="abs btn-outline">CONTACT US</div>
</header>

<section>
  <h2 class="abs welcome-title">WELCOME TO <span>BRISK HARBOR</span></h2>
  <p class="abs welcome-text">We are a Claims Recovery and Debt Management Services company based in Dubai, United Arab Emirates. The Brisk Harbor team handles a comprehensive range of debt recoveries, such as invoices; insurance payments; supplier and rent payments; and personal and business loans, for individuals and businesses across an array of industries.</p>

  <div class="abs sector" style="left:81px">
    <div class="sector-icon"><svg width="54" height="50" viewBox="0 0 54 50"><path d="M27 2 52 14H2Z" fill="#27496d"/><rect x="4" y="16" width="46" height="4" fill="#27496d"/><rect x="8" y="22" width="6" height="18" fill="#27496d"/><rect x="19" y="22" width="6" height="18" fill="#27496d"/><rect x="30" y="22" width="6" height="18" fill="#27496d"/><rect x="41" y="22" width="6" height="18" fill="#27496d"/><rect x="2" y="42" width="50" height="6" fill="#27496d"/></svg></div>
    <div class="sector-label">GOVERNMENT<br>ENTITIES</div>
  </div>
  <div class="abs sector" style="left:350px">
    <div class="sector-icon"><svg width="56" height="50" viewBox="0 0 56 50"><path d="M28 48 6 26C-2 17 4 2 16 2c6 0 10 4 12 7 2-3 6-7 12-7 12 0 18 15 10 24Z" fill="#27496d"/><path d="M6 25h14l4-8 6 16 5-10 3 2h12" fill="none" stroke="#e9e9e9" stroke-width="3"/></svg></div>
    <div class="sector-label">MEDICAL &amp; HEALTH<br>CARE</div>
  </div>
  <div class="abs sector" style="left:620px">
    <div class="sector-icon"><svg width="34" height="56" viewBox="0 0 34 56"><text x="17" y="47" text-anchor="middle" font-family="Lato,sans-serif" font-weight="900" font-size="52" fill="#27496d">$</text></svg></div>
    <div class="sector-label">BANKS &amp; FINANCE<br>COMPANIES</div>
  </div>
  <div class="abs sector" style="left:889px">
    <div class="sector-icon"><svg width="60" height="40" viewBox="0 0 60 40"><path d="M2 8 14 4 22 10 14 22Z" fill="#27496d"/><path d="M58 8 46 4 38 10 46 22Z" fill="#27496d"/><path d="M18 12 30 6 44 18 34 30 22 22Z" fill="#27496d"/></svg></div>
    <div class="sector-label">SME'S &amp; COMMERCIAL<br>BUSINESS</div>
  </div>
</section>

<section class="abs band-grey" style="top:1340px;height:395px"></section>
<div class="abs recovery-art" role="img" aria-label="Illustration of a tablet showing a rising bar chart with a red arrow and a pie chart"></div>
<h2 class="abs section-title" style="left:602px;top:1390px">RECOVERY SOLUTIONS</h2>
<div class="abs copy" style="left:602px;top:1448px;width:520px">
  <p>Our experience has taught us that when it comes to recovery, it always pays to find the most amicable solution, and we work hard to make this happen.</p>
  <p>The Brisk Harbor team is trained in communication, and we believe that this is part of our success.</p>
</div>
<div class="abs btn" style="left:600px;top:1625px;width:167px">READ MORE</div>

<h2 class="abs section-title" style="left:80px;top:1780px">DEBT MANAGEMENT</h2>
<div class="abs copy" style="left:80px;top:1838px;width:490px">
  <p>At Brisk Harbor, we pull together our wisdom and expertise to make debt work for you.</p>
  <p>Our debt management services bring together thorough analysis, careful planning and realistic budgeting to help you manage your debt.</p>
</div>
<div class="abs btn" style="left:78px;top:2012px;width:166px;height:52px">READ MORE</div>

<svg class="abs" style="left:624px;top:1802px" width="497" height="342" viewBox="0 0 497 342">
  <line x1="248" y1="80" x2="248" y2="146" stroke="#27496d" stroke-width="2"/>
  <line x1="124" y1="187" x2="374" y2="187" stroke="#9a9a9a" stroke-width="2"/>
</svg>
<div class="abs node lead" style="left:811px;top:1802px">DEBT<br>MANAGEMNT</div>
<div class="abs node" style="left:624px;top:1947px">DEBT<br>COUNSELLING</div>
<div class="abs node" style="left:811px;top:1947px">DEBT<br>RESTRUCTURI<br>NG</div>
<div class="abs node" style="left:998px;top:1947px">DEBT<br>SETTLEMENT</div>
<div class="abs node" style="left:717px;top:2061px">Outsourcing</div>
<div class="abs node" style="left:910px;top:2061px">Interactive<br>Online Access</div>

<section class="abs band-grey" style="top:2218px;height:449px"></section>
<h2 class="abs news-title">RECENT <span>NEWS</span></h2>

<article class="abs news-card" style="left:78px">
  <div class="news-photo" role="img" aria-label="Photo of a business meeting in an office" style="background:linear-gradient(135deg,#cfd8dc,#7f8c99)"></div>
  <div class="news-head">Lorem Ipsum is dummy text.</div>
  <div class="news-date"><svg width="12" height="12" viewBox="0 0 12 12"><rect x="1" y="2" width="10" height="9" fill="#aaa"/></svg>11 June 2016</div>
  <p class="news-text">Lorem Ipsum is simply dummy text of the printing and type setting industry.</p>
</article>
<article class="abs news-card" style="left:348px">
  <div class="news-photo" role="img" aria-label="Photo of colleagues working together at a desk" style="background:linear-gradient(135deg,#e6e2dc,#8a7f73)"></div>
  <div class="news-head">Lorem Ipsum is dummy text.</div>
  <div class="news-date"><svg width="12" height="12" viewBox="0 0 12 12"><rect x="1" y="2" width="10" height="9" fill="#aaa"/></svg>10 June 2016</div>
  <p class="news-text">Lorem Ipsum is simply dummy text of the printing and type setting industry.</p>
</article>
<article class="abs news-card" style="left:620px">
  <div class="news-photo" role="img" aria-label="Photo of a business handshake" style="background:linear-gradient(135deg,#9aa6b4,#3c4856)"></div>
  <div class="news-head">Lorem Ipsum is dummy text.</div>
  <div class="news-date"><svg width="12" height="12" viewBox="0 0 12 12"><rect x="1" y="2" width="10" height="9" fill="#aaa"/></svg>09 June 2016</div>
  <p class="news-text">Lorem Ipsum is simply dummy text of the printing and type setting industry.</p>
</article>
<article class="abs news-card" style="left:888px">
  <div class="news-photo" role="img" aria-label="Photo of blue glass office towers" style="background:linear-gradient(135deg,#6d9bd1,#1f4f8f)"></div>
  <div class="news-head">Lorem Ipsum is dummy text.</div>
  <div class="news-date"><svg width="12" height="12" viewBox="0 0 12 12"><rect x="1" y="2" width="10" height="9" fill="#aaa"/></svg>08 June 2016</div>
  <p class="news-text">Lorem Ipsum is simply dummy text of the printing and type setting industry.</p>
</article>

<footer class="abs footer"></footer>
<div class="abs foot-brand">BRISK HARBOR</div>
<p class="abs foot-about">We are a Claims Recovery and Debt Management Services company based in Dubai.</p>

<div class="abs foot-heading" style="left:350px">USEFUL LINKS</div>
<ul class="abs foot-links" style="color:#fff">
  <li style="color:#fff">Home</li><li style="color:#fff">About</li><li style="color:#fff">Services</li><li style="color:#fff">Clients</li><li style="color:#fff">Blog</li><li style="color:#fff">Contact</li>
</ul>

<div class="abs foot-heading" style="left:620px">NEWSLETTER</div>
<div class="abs" style="left:620px;top:2745px;font-size:15px;color:#fff">Subscribe to stay on Brisk Harbor</div>
<div class="abs field" style="top:2782px;color:#fff">Enter Name</div>
<div class="abs field" style="top:2832px;color:#fff">Enter Email</div>
<div class="abs subscribe"><span>SUBSCRIBE</span></div>

<div class="abs foot-heading" style="left:892px">GET IN TOUCH</div>
<div class="abs contact-row" style="top:2743px;color:#fff">
  <svg width="14" height="22" viewBox="0 0 14 22"><path d="M7 0C3 0 0 3 0 7c0 5 7 15 7 15s7-10 7-15c0-4-3-7-7-7Z" fill="#fff"/><circle cx="7" cy="7" r="2.5" fill="#27496d"/></svg>
  <span style="color:#fff">Lorem Ipsum is dummy<br>text of the printing.</span>
</div>
<div class="abs contact-row" style="top:2804px;font-weight:700;color:#fff">
  <svg width="18" height="18" viewBox="0 0 18 18"><path d="M4 1 7 5 5 7c1 3 3 5 6 6l2-2 4 3-2 3C8 17 1 10 1 3Z" fill="#fff"/></svg>
  <span style="color:#fff">123 456 7890</span>
</div>
<div class="abs contact-row" style="top:2838px;color:#fff">
  <svg width="18" height="14" viewBox="0 0 18 14"><rect x="1" y="1" width="16" height="12" fill="none" stroke="#fff" stroke-width="2"/><path d="M1 1 9 8 17 1" fill="none" stroke="#fff" stroke-width="2"/></svg>
  <span style="color:#fff">info@briskharbor.com</span>
</div>
<div class="abs social" style="left:885px" role="img" aria-label="Social profile link"></div>
<div class="abs social" style="left:957px" role="img" aria-label="Social profile link"></div>
<div class="abs social" style="left:1031px" role="img" aria-label="Social profile link"></div>

<div class="abs foot-rule"></div>
<div class="abs copyright" style="color:#fff">© <b style="color:#fff">BRISK HARBOR</b> - 2016. All Rights Reserved.</div>

</body>
</html>
```